Need Help having my business card stand out

I am the owner of Birchway Canine Training and would like for my business cards to stand out. I have been trying to keep designing them myself but I can't get what I have in my head on the card. I will try my best to post templates that I like for inspirations. I want something unique but elegant. I don't want in to look cartoony or cheesy. It needs to pop in a pet shop but also in a coffee shop or gym.

Target Market(s)

Dog owners, Married ,No young kids Jr High school kids and up (maybe kids on the way) Executives, Stay at home moms/wives, Small business owners

Industry/Entity Type

Dog Training

Contact Information for Business Card

Lowell Spratt, 281-904-3376, info@birchwaycanine.example, www.birchwaycanine.example

Colors

Designer to choose colors to be used in the design.

Requirements
Must have
• my logo
Should not have
• Cursive lettering

```html
<!DOCTYPE html>
<html lang="en">
<head>
<meta charset="utf-8">
<title>Birchway Canine Training – Business Card</title>
<link rel="stylesheet" href="https://fonts.googleapis.com/css2?family=Roboto:wght@400;500&display=swap">
<style>
  :root {
    --stage: #e9e7e4;
    --ink: #0c0c0c;
    --paper: #ffffff;
    --paper-soft: #f4f4f4;
    --muted: #6a6a6a;
    --icon-box: #3a3a3a;
  }
  * { box-sizing: border-box; margin: 0; padding: 0; }
  html, body { width: 1200px; height: 810px; overflow: hidden; }
  body {
    background: var(--stage);
    font-family: "Roboto", Arial, sans-serif;
    position: relative;
  }
  .card {
    position: absolute;
    width: 525px;
    height: 300px;
    overflow: hidden;
    box-shadow: 0 8px 24px rgba(0,0,0,0.18);
  }
  .card--front { left: 45px; top: 255px; background: var(--ink); }
  .card--back  { left: 630px; top: 255px; background: linear-gradient(160deg, #1a1a1a, var(--ink) 60%); color: var(--paper); }

  .front__band {
    position: absolute;
    left: 0; right: 0;
    top: 60px; height: 180px;
    background: var(--paper-soft);
    display: flex;
    align-items: center;
    justify-content: center;
  }
  .wordmark {
    display: flex;
    align-items: center;
    gap: 10px;
    font-weight: 500;
    font-size: 20px;
    letter-spacing: 0.5px;
  }
  .wordmark__dot {
    width: 14px; height: 14px;
    border-radius: 50%;
    background: currentColor;
    flex: none;
  }
  .front__band .wordmark { color: var(--ink); }

  .back__wordmark {
    position: absolute;
    top: 58px;
    left: 300px;
    transform: translateX(-50%);
    white-space: nowrap;
    color: var(--paper);
  }
  .back__name {
    position: absolute;
    left: 40px;
    top: 158px;
    font-size: 20px;
    font-weight: 400;
    letter-spacing: 0.5px;
    text-transform: uppercase;
  }
  .back__divider {
    position: absolute;
    left: 250px;
    top: 150px;
    width: 2px;
    height: 120px;
    background: var(--paper);
  }
  .contact-list {
    position: absolute;
    left: 268px;
    top: 160px;
    list-style: none;
    font-size: 14.5px;
  }
  .contact-list li {
    display: flex;
    align-items: center;
    gap: 10px;
    height: 26px;
  }
  .contact-list li.contact--phone { margin-bottom: 14px; }
  .contact-icon {
    width: 14px; height: 14px;
    background: var(--icon-box);
    border-radius: 2px;
    flex: none;
  }
</style>
</head>
<body>
  <section class="card card--front" aria-label="Card front">
    <div class="front__band">
      <div class="wordmark"><span class="wordmark__dot"></span>Birchway Canine Training</div>
    </div>
  </section>

  <section class="card card--back" aria-label="Card back">
    <div class="wordmark back__wordmark"><span class="wordmark__dot"></span>Birchway Canine Training</div>
    <h1 class="back__name">Lowell Spratt</h1>
    <div class="back__divider"></div>
    <ul class="contact-list">
      <li class="contact--phone">
        <svg class="contact-icon" viewBox="0 0 14 14"><rect width="14" height="14" rx="2" fill="#3a3a3a"/><path d="M4 3.5c.6-.4 1.2-.2 1.4.3l.5 1.2c.1.3 0 .6-.2.8l-.5.4c.4.9 1.1 1.6 2 2l.4-.5c.2-.2.5-.3.8-.2l1.2.5c.5.2.7.8.3 1.4-.5.7-1.3.9-2.1.6C6 9.4 4.6 8 4 6.2c-.3-.9-.1-1.9.0-2.7z" fill="#9a9a9a"/></svg>
        281-904-3376
      </li>
      <li>
        <svg class="contact-icon" viewBox="0 0 14 14"><rect width="14" height="14" rx="2" fill="#3a3a3a"/><rect x="3" y="4.5" width="8" height="5.5" fill="none" stroke="#9a9a9a" stroke-width="1"/><path d="M3 4.5l4 3 4-3" fill="none" stroke="#9a9a9a" stroke-width="1"/></svg>
        info@birchwaycanine.example
      </li>
      <li>
        <svg class="contact-icon" viewBox="0 0 14 14"><rect width="14" height="14" rx="2" fill="#3a3a3a"/><circle cx="7" cy="7" r="3.8" fill="none" stroke="#9a9a9a" stroke-width="1"/><path d="M3.2 7h7.6M7 3.2c-1.5 2-1.5 5.6 0 7.6M7 3.2c1.5 2 1.5 5.6 0 7.6" fill="none" stroke="#9a9a9a" stroke-width="0.8"/></svg>
        www.birchwaycanine.example
      </li>
    </ul>
  </section>
</body>
</html>
```